Revamp of existing namecard

Existingly, i've got a namecard that i would like to retain the main design. but there are some changes in my company and i would need to do some amendments to it.

We are a money transfer and money exchange company.
I need 2 different types of name card.
1. For individual name cards
the front to put the following:
Company name and logo
English Name, Chinese Name appointment
Mobile Number, Email and Website.
2 License number under the logo and name

the back of the name card to put
8 address: 7 Singapore and 1 Hong Kong branch addresses
8 Mobile Number of the corresponding addresses.

We would like to retain the name card front design
the name card back design can change but color to retain.

2nd name card is generic name card
Front:
Company name and logo
Branch Mobile Number, Branch Address, Email and Website.

Industry/Entity Type

remittance and money exchange

Contact Information for Business Card

I need 2 different types of name card. 1. For individual name cards the front to put the following: Company name and logo English Name, Chinese Name appointment Mobile Number, Email and Website. 2 License number under the logo and name the back of the name card to put 8 address: 7 Singapore and 1 Hong Kong branch addresses 8 Mobile Number of the corresponding addresses. We would like to retain the name card front design the name card back design can change but color to retain. 2nd name card is generic name card Front: the front to put the following: Company name and logo Branch Mobile Number, Branch Address, Email and Website. 2 License number under the logo and name

Requirements
Must have
• I need 2 different types of name card. 1. For individual name cards the front to put the following: Company name and logo English Name, Chinese Name appointment Mobile Number, Email and Website. 2 License number under the logo and name the back of the name card to put 8 address: 7 Singapore and 1 Hong Kong branch addresses 8 Mobile Number of the corresponding addresses. We would like to retain the name card front design the name card back design can change but color to retain. 2nd name card is generic name card Front: the front to put the following: Company name and logo Branch Mobile Number, Branch Address, Email and Website. 2 License number under the logo and name
Nice to have
• use back color code

```html
<!DOCTYPE html>
<html lang="en">
<head>
<meta charset="utf-8">
<title>Meridane Name Card</title>
<link href="https://fonts.googleapis.com/css2?family=Montserrat:wght@400;500;600;700&family=Noto+Sans+SC:wght@700&display=swap" rel="stylesheet">
<style>
  :root{
    --backdrop:#d6d8db;
    --paper:#ffffff;
    --ink:#111418;
    --accent:#1f95c0;
    --navy:#252e3c;
    --navy-deep:#1b222d;
    --map-light:#e3e4e6;
    --map-dark:#151b24;
    --rule:#3f6f86;
  }
  *{margin:0;padding:0;box-sizing:border-box}
  html,body{width:1200px;height:857px;overflow:hidden;background:var(--backdrop);font-family:"Montserrat",sans-serif}
  .stage{position:relative;width:1200px;height:857px}
  .card{position:absolute;top:274px;width:540px;height:309px;overflow:hidden;box-shadow:0 10px 28px rgba(0,0,0,.18)}
  .card--front{left:40px;background:var(--paper)}
  .card--back{left:620px;background:var(--navy)}

  .world-map{position:absolute;border-radius:40% 45% 35% 50%}
  .card--front .world-map{left:40px;top:50px;width:460px;height:230px;background:radial-gradient(ellipse at 50% 45%,#d2d3d6 0%,var(--map-light) 55%,rgba(255,255,255,0) 75%)}
  .card--back .world-map{left:30px;top:40px;width:480px;height:240px;background:radial-gradient(ellipse at 50% 45%,var(--map-dark) 0%,var(--navy-deep) 50%,rgba(37,46,60,0) 75%)}

  .brand{position:absolute;right:34px;top:30px;display:flex;align-items:center;gap:10px}
  .brand__mark{width:34px;height:34px;border-radius:50%;background:var(--accent)}
  .brand__name{font-weight:700;font-size:32px;letter-spacing:2px;color:var(--ink);line-height:1}
  .brand__licence{position:absolute;right:34px;top:68px;font-size:10px;font-weight:500;letter-spacing:2px;color:var(--ink)}

  .contact{position:absolute;left:250px;top:110px;list-style:none}
  .contact li{display:flex;align-items:center;gap:8px;font-size:12.5px;font-weight:600;letter-spacing:1.2px;color:var(--ink);height:20px}
  .contact svg{width:12px;height:12px;flex:none;fill:var(--accent)}

  .person{position:absolute;left:36px;top:200px}
  .person__name{font-weight:700;font-size:24px;color:var(--ink);line-height:1.05}
  .person__name-zh{font-family:"Noto Sans SC",sans-serif;font-weight:700;font-size:22px;color:var(--ink);line-height:1.15}
  .person__role{font-size:13px;font-weight:500;color:var(--accent);letter-spacing:.6px}

  .branch-head{position:absolute;display:flex;align-items:flex-start;gap:6px;color:var(--paper)}
  .branch-head svg{width:10px;height:14px;margin-top:4px;fill:var(--accent)}
  .branch-head__city{font-size:16px;font-weight:500;letter-spacing:.5px;line-height:1.1}
  .branch-head__tag{font-size:7px;color:var(--accent);margin-left:4px}
  .branch-head__licence{display:block;font-size:6.5px;letter-spacing:1px;color:#c9ced6}
  .branch-head--sg{left:150px;top:34px}
  .branch-head--hk{left:200px;top:212px}

  .branches{position:absolute;list-style:none}
  .branches li{text-align:center;padding:3px 0 4px;border-bottom:1px solid var(--rule);margin-bottom:5px;width:200px}
  .branches__addr{display:block;font-size:7px;color:#e8ebef;letter-spacing:.3px}
  .branches__phone{display:block;font-size:7px;color:var(--accent);letter-spacing:.3px}
  .branches--right{left:300px;top:38px}
  .branches--left{left:40px;top:108px}
  .branches--hk{left:190px;top:246px}
</style>
</head>
<body>
<main class="stage">

  <section class="card card--front" aria-label="Name card front">
    <div class="world-map" role="img" aria-label="Dotted world map in light grey"></div>
    <div class="brand">
      <span class="brand__mark"></span>
      <span class="brand__name">MERIDANE</span>
    </div>
    <p class="brand__licence">01234567 | 01234567</p>

    <ul class="contact">
      <li><svg viewBox="0 0 12 12"><path d="M3 0h6a1 1 0 0 1 1 1v10a1 1 0 0 1-1 1H3a1 1 0 0 1-1-1V1a1 1 0 0 1 1-1zm0 1.5v8h6v-8z"/></svg>+852 5550 1234</li>
      <li><svg viewBox="0 0 12 12"><path d="M2.5 0.5l2 2.5-1.2 1.5a7 7 0 0 0 4.2 4.2L9 7.5l2.5 2-1.5 2C5 11 1 7 0.5 2z"/></svg>+852 5550 1234</li>
      <li><svg viewBox="0 0 12 12"><path d="M0 2h12v8H0zm1 1v.4l5 3.3 5-3.3V3z"/></svg>marcus@meridane.com.hk</li>
      <li><svg viewBox="0 0 12 12"><path d="M6 0a6 6 0 1 0 0 12A6 6 0 0 0 6 0zm0 1c.8 0 1.6 1.9 1.7 4.5H4.3C4.4 2.9 5.2 1 6 1zM1 6.5h2.3c.1 1.6.4 3 .9 3.9A5 5 0 0 1 1 6.5zm0-1a5 5 0 0 1 3.2-3.9c-.5.9-.8 2.3-.9 3.9zm3.3 1h3.4C7.6 9 6.8 11 6 11S4.4 9 4.3 6.5zm4.4 0H11a5 5 0 0 1-3.2 3.9c.5-.9.8-2.3.9-3.9zm0-1c-.1-1.6-.4-3-.9-3.9A5 5 0 0 1 11 5.5z"/></svg>www.meridane.com.hk</li>
    </ul>

    <div class="person">
      <p class="person__name">Marcus Lim</p>
      <p class="person__name-zh">林志明</p>
      <p class="person__role">Director of Business Development</p>
    </div>
  </section>

  <section class="card card--back" aria-label="Name card back">
    <div class="world-map" role="img" aria-label="Dotted world map in dark navy"></div>

    <div class="branch-head branch-head--sg">
      <svg viewBox="0 0 10 14"><path d="M5 0a5 5 0 0 1 5 5c0 3.5-5 9-5 9S0 8.5 0 5a5 5 0 0 1 5-5zm0 3a2 2 0 1 0 0 4 2 2 0 0 0 0-4z"/></svg>
      <div>
        <span class="branch-head__city">Singapore<span class="branch-head__tag">Branch</span></span>
        <span class="branch-head__licence">01234567 | 01234567</span>
      </div>
    </div>

    <ul class="branches branches--right">
      <li><span class="branches__addr">Harbour Plaza #01-00, 12 Example Road, 100001</span><span class="branches__phone">+65 5550 2001</span></li>
      <li><span class="branches__addr">Harbour Plaza #01-00, 12 Example Road, 100001</span><span class="branches__phone">+65 5550 2001</span></li>
      <li><span class="branches__addr">Harbour Plaza #01-00, 12 Example Road, 100001</span><span class="branches__phone">+65 5550 2001</span></li>
      <li><span class="branches__addr">Harbour Plaza #01-00, 12 Example Road, 100001</span><span class="branches__phone">+65 5550 2001</span></li>
    </ul>

    <ul class="branches branches--left">
      <li><span class="branches__addr">Harbour Plaza #01-00, 12 Example Road, 100001</span><span class="branches__phone">+65 5550 2001</span></li>
      <li><span class="branches__addr">Harbour Plaza #01-00, 12 Example Road, 100001</span><span class="branches__phone">+65 5550 2001</span></li>
      <li><span class="branches__addr">Harbour Plaza #01-00, 12 Example Road, 100001</span><span class="branches__phone">+65 5550 2001</span></li>
    </ul>

    <div class="branch-head branch-head--hk">
      <svg viewBox="0 0 10 14"><path d="M5 0a5 5 0 0 1 5 5c0 3.5-5 9-5 9S0 8.5 0 5a5 5 0 0 1 5-5zm0 3a2 2 0 1 0 0 4 2 2 0 0 0 0-4z"/></svg>
      <div>
        <span class="branch-head__city">Hong Kong<span class="branch-head__tag">Branch</span></span>
        <span class="branch-head__licence">01234567 | 01234567</span>
      </div>
    </div>

    <ul class="branches branches--hk">
      <li><span class="branches__addr">Harbour Plaza #01-00, 12 Example Road, 100001</span><span class="branches__phone">+65 5550 2001</span></li>
    </ul>
  </section>

</main>
</body>
</html>
```